13 Varno - new website design project

Our company Varno Electrical is developing a new lead generation website focused on Electrical, LED Lighting and Solar Power. We need a high converting website.

Example of our current website is www.varnoelectrical-example.com.au You can take content from this website for this new design. Our colours are red, black and white. For our new website we would like to promote Varno, Spark Every Day. Please listen to the jingle.

The below link is the company jingle that we have developed.
http://www.tunecraftdemo.com.au/vrn-tc-v1/

The key for this brief is to generate leads for Electrical, LED Lighting (for commercial) and Solar Power & Storage.

Target Market(s)

Business owners in Melbourne Victoria

Number of Pages Required

4 page

Colors
ec1f27
ffffff

Requirements
Must have
• This page must be clean, be in line with company branding and a high converting lead website.

```html
<!DOCTYPE html>
<html lang="en">
<head>
<meta charset="utf-8">
<title>Varno Electrical – Electrical, LED Lighting, Solar Power</title>
<link href="https://fonts.googleapis.com/css2?family=Roboto:wght@400;500;700&family=Roboto+Condensed:wght@400;700&family=Open+Sans:ital,wght@0,400;0,600;1,400&display=swap" rel="stylesheet">
<style>
:root{
  --red:#d71f26;
  --red-dark:#b8181e;
  --ink:#222;
  --text:#555;
  --muted:#888;
  --nav:#2c2e34;
  --footer:#2a2c31;
  --navy:#142238;
  --grey-bg:#f3f3f3;
  --white:#fff;
}
*{margin:0;padding:0;box-sizing:border-box}
html,body{width:1200px;height:3030px;overflow:hidden;background:var(--white)}
body{font-family:"Open Sans",sans-serif;color:var(--text);position:relative}
.abs{position:absolute}
/* header */
.site-header{position:absolute;left:0;top:0;width:1200px;height:133px;background:var(--white)}
.brand{position:absolute;left:100px;top:20px;display:flex;align-items:flex-start;gap:10px}
.brand-mark{width:22px;height:22px;background:var(--red);margin-top:14px}
.brand-name{font-family:"Roboto Condensed",sans-serif;font-weight:700;font-size:44px;line-height:1;color:var(--ink);letter-spacing:1px}
.brand-tag{font-family:"Roboto Condensed",sans-serif;font-weight:700;font-size:15px;color:var(--ink);margin-top:4px}
.call{position:absolute;left:650px;top:40px;display:flex;gap:12px;align-items:center}
.call svg{width:34px;height:34px}
.call small{display:block;font-family:"Roboto",sans-serif;color:var(--red);font-size:15px;line-height:1}
.call strong{font-family:"Roboto",sans-serif;font-weight:400;font-size:21px;color:var(--ink)}
.search{position:absolute;left:868px;top:46px;width:232px;height:36px;border:1px solid #ccc;display:flex}
.search span{flex:1;font-size:11px;color:#888;padding:10px 10px}
.search i{width:36px;background:#e4e4e4;border-left:1px solid #ccc;display:flex;align-items:center;justify-content:center}
/* nav */
.main-nav{position:absolute;left:0;top:133px;width:1200px;height:49px;background:var(--nav);display:flex;padding-left:98px}
.main-nav a{font-family:"Roboto",sans-serif;font-size:13px;color:#fff;text-decoration:none;padding:0 24px;line-height:49px;text-transform:uppercase}
.main-nav a.active{background:var(--red)}
/* hero */
.hero{position:absolute;left:0;top:182px;width:1200px;height:555px;background:radial-gradient(ellipse at 62% 45%,#2a4a6a 0%,#172a45 45%,var(--navy) 100%)}
.hero-art{position:absolute;left:430px;top:30px;width:580px;height:460px;border-radius:50%;background:radial-gradient(circle at 50% 50%,#8be04a 0%,#3c9b2c 35%,rgba(30,80,60,.4) 65%,rgba(20,34,56,0) 75%)}
.hero-title{position:absolute;left:97px;top:170px;font-family:"Roboto Condensed",sans-serif;font-weight:700;font-size:46px;color:#fff;line-height:1}
.hero-sub{position:absolute;left:97px;top:228px;font-family:"Roboto Condensed",sans-serif;font-weight:700;font-size:22px;color:#fff}
.btn{display:inline-block;background:var(--red);color:#fff;font-family:"Roboto",sans-serif;font-size:15px;border-radius:3px;text-align:center}
.hero .btn{position:absolute;left:97px;top:276px;width:117px;height:34px;line-height:34px}
.dots{position:absolute;left:97px;top:330px;display:flex;gap:6px}
.dots b{width:11px;height:11px;border-radius:50%;background:#fff}
.dots b:first-child{box-shadow:0 0 0 2px var(--navy),0 0 0 3px #fff}
.hero-cut{position:absolute;left:0;top:479px}
/* services */
.services{position:absolute;left:0;top:737px;width:1200px;height:433px;background:var(--grey-bg)}
.section-title{font-family:"Roboto",sans-serif;font-weight:400;color:var(--ink);text-align:center;text-transform:uppercase}
.services .section-title{position:absolute;left:0;top:0;width:1200px;font-size:28px;top:0}
.service{position:absolute;top:73px;width:310px}
.service-photo{height:183px}
.service h3{font-family:"Roboto",sans-serif;font-weight:400;font-size:18px;color:var(--ink);margin:20px 0 8px}
.service p{font-size:11px;line-height:20px}
/* about */
.about-art{position:absolute;left:120px;top:1230px;width:300px;height:300px;border-radius:50%;background:radial-gradient(circle at 45% 40%,#f2f2f2 0%,#c9c9c9 45%,#7cc243 70%,#fff 72%)}
.about-text{position:absolute;left:467px;top:1258px;width:640px}
.about-text h2{font-family:"Roboto",sans-serif;font-weight:400;font-size:27px;color:var(--ink);margin-bottom:14px}
.about-text h2 span{color:var(--red)}
.about-text p{font-size:11px;line-height:21px;margin-bottom:12px}
.about-text .btn{font-size:13px;padding:0 14px;height:32px;line-height:32px;margin-top:6px}
/* why */
.why{position:absolute;left:0;top:1610px;width:1200px;height:500px;background:var(--grey-bg)}
.why .section-title{position:absolute;top:50px;width:1200px;font-size:32px}
.why-rule{position:absolute;left:535px;top:100px;width:130px;height:2px;background:var(--red)}
.why-rule::after{content:"";position:absolute;left:60px;top:-3px;width:10px;height:8px;background:var(--red);transform:skewX(-20deg)}
.reason{position:absolute;top:157px;width:180px;height:155px;display:flex;flex-direction:column;align-items:center;justify-content:flex-end;padding-bottom:22px;clip-path:polygon(18% 0,100% 0,82% 100%,0 100%);color:#fff;font-family:"Roboto",sans-serif;font-size:14px;text-align:center;line-height:17px}
.reason svg{width:46px;height:46px;margin-bottom:14px}
.reason.red{background:var(--red)}
.reason.dark{background:var(--nav)}
.arrow{position:absolute;top:228px}
.pointer{position:absolute;left:379px;top:312px;border:12px solid transparent;border-top-color:var(--nav)}
.detail{position:absolute;left:348px;top:365px;width:640px}
.detail h3{display:flex;align-items:center;gap:14px;font-family:"Roboto",sans-serif;font-weight:400;font-size:24px;color:var(--ink)}
.detail h3 b{width:28px;height:28px;border-radius:50%;background:var(--ink);color:#fff;font-size:15px;text-align:center;line-height:28px}
.detail p{font-size:12px;line-height:25px;margin-top:14px}
/* clients */
.clients .section-title{position:absolute;top:2160px;width:1200px;font-size:34px;text-transform:none}
.client{position:absolute;top:2232px;width:138px;height:80px;display:flex;align-items:center;justify-content:center;font-family:"Roboto",sans-serif;font-weight:500;font-size:17px;color:var(--ink);text-align:center}
/* testimonials */
.testimonials{position:absolute;left:0;top:2385px;width:1200px;height:295px;background:var(--grey-bg)}
.quote{position:absolute;top:76px;width:480px}
.quote-photo{position:absolute;left:0;top:0;width:120px;height:120px;border-radius:50%;border:4px solid #fff}
.quote-body{position:absolute;left:140px;top:4px;width:320px}
.quote-body p{font-style:italic;font-size:11px;line-height:21px;color:#666}
.quote-body cite{display:block;margin-top:12px;font-style:normal;font-size:12px;line-height:17px;color:var(--red)}
.quote-mark{position:absolute;left:400px;top:98px;font-family:Georgia,serif;font-size:64px;color:#bbb;line-height:1}
/* footer */
.site-footer{position:absolute;left:0;top:2680px;width:1200px;height:350px;background:var(--footer);color:#ddd;font-size:12px}
.site-footer h4{font-family:"Roboto",sans-serif;font-weight:400;font-size:17px;color:#fff;text-transform:uppercase;margin-bottom:18px}
.foot-brand{position:absolute;left:100px;top:40px}
.foot-brand .brand-name{color:#fff;font-size:36px}
.foot-brand .brand-tag{color:#fff;font-size:12px}
.foot-brand address{font-style:normal;margin-top:26px;line-height:18px}
.foot-line{display:flex;align-items:center;gap:12px;margin-top:12px}
.newsletter{position:absolute;left:418px;top:40px;width:260px}
.newsletter p{line-height:20px;margin-bottom:14px}
.newsletter .field{width:256px;height:38px;background:#fff;color:#777;font-size:11px;padding:12px 10px}
.newsletter .btn{margin-top:12px;font-size:12px;padding:0 16px;height:38px;line-height:38px}
.links{position:absolute;left:793px;top:40px}
.links li{list-style:none;line-height:21px}
.links li::before{content:"";display:inline-block;border:4px solid transparent;border-left-color:#fff;margin-right:10px}
.social{position:absolute;left:998px;top:40px}
.social li{list-style:none;display:flex;align-items:center;gap:10px;margin-bottom:10px}
.social li::before{content:"";width:24px;height:24px;border:1px solid #bbb;border-radius:50%}
.copyright{position:absolute;left:0;top:270px;width:1200px;border-top:1px solid #3c3e44;text-align:center;padding-top:30px;font-size:11px}
</style>
</head>
<body>

<header class="site-header">
  <div class="brand">
    <span class="brand-mark"></span>
    <div><div class="brand-name">VARNO</div><div class="brand-tag">Spark Every Day</div></div>
  </div>
  <div class="call">
    <svg viewBox="0 0 34 34"><circle cx="17" cy="17" r="15" fill="none" stroke="#d71f26" stroke-width="2"/><path d="M12 10c1-1 2-1 3 0l1 3-2 2c1 2 3 4 5 5l2-2 3 1c1 1 1 2 0 3-2 2-6 1-9-2s-5-7-3-10z" fill="#d71f26"/></svg>
    <div><small>Call Us</small><strong>+ 139057 Varno</strong></div>
  </div>
  <div class="search"><span>Search</span><i><svg width="12" height="12" viewBox="0 0 12 12"><circle cx="5" cy="5" r="3.5" fill="none" stroke="#555" stroke-width="1.5"/><path d="M7.5 7.5l3 3" stroke="#555" stroke-width="1.5"/></svg></i></div>
</header>

<nav class="main-nav">
  <a class="active">Home</a><a>Varno Story</a><a>Our Work</a><a>Electrical</a><a>LED Lighting</a><a>Solar Power</a><a>Contact Us</a>
</nav>

<section class="hero">
  <div class="hero-art" role="img" aria-label="Green globe with a power plug, wind turbines, trees and a solar panel"></div>
  <h1 class="hero-title">VARNO ELECTRICAL</h1>
  <p class="hero-sub">ELECTRICAL.LED LIGHTING.SOLAR POWER</p>
  <span class="btn">Read More</span>
  <div class="dots"><b></b><b></b><b></b><b></b></div>
  <svg class="hero-cut" width="1200" height="80" viewBox="0 0 1200 80"><polygon points="0,80 600,0 1200,80" fill="#f3f3f3"/></svg>
</section>

<section class="services">
  <h2 class="section-title" style="top:0">Our Services</h2>
  <article class="service" style="left:98px">
    <div class="service-photo" role="img" aria-label="Electrician working at a switchboard" style="background:linear-gradient(135deg,#c9ccd1,#6c7a8c)"></div>
    <h3>ELECTRICAL</h3>
    <p>Sed ut perspiciatis unde omnis iste natus error sit voluptatem accusantium doloremque laudantium, totam rem aperiam, eaque ipsa quae ab</p>
  </article>
  <article class="service" style="left:445px">
    <div class="service-photo" role="img" aria-label="Warehouse ceiling fitted with LED lighting" style="background:linear-gradient(180deg,#d8dce2,#8f98a4)"></div>
    <h3>LED LIGHTING</h3>
    <p>Sed ut perspiciatis unde omnis iste natus error sit voluptatem accusantium doloremque laudantium, totam rem aperiam, eaque ipsa quae ab</p>
  </article>
  <article class="service" style="left:790px">
    <div class="service-photo" role="img" aria-label="Installer fitting solar panels on a roof" style="background:linear-gradient(160deg,#6fa3d8,#2a4f8a)"></div>
    <h3>SOLAR POWER</h3>
    <p>Sed ut perspiciatis unde omnis iste natus error sit voluptatem accusantium doloremque laudantium, totam rem aperiam, eaque ipsa quae ab</p>
  </article>
</section>

<section class="about">
  <div class="about-art" role="img" aria-label="LED bulb with a green leaf swirl"></div>
  <div class="about-text">
    <h2>ABOUTUS <span>VARNO ELECTRICAL</span></h2>
    <p>Electrical and Energy Solutions are at the forefront of our company. Varno Electrical has a long history in Electrical, LED Lighting and Solar Power and just like the Cougar, we will strive to be fierce &amp; agile in an effort to exceed our customer's expectations and develop stronger links with all our business partners &amp; community.</p>
    <p>Varno Electrical is an expert Electrical Company providing services to all Residential and Commercial customers. With over 10 years of experience, Varno Electrical has developed a highly-experienced team of professionals that ensure all our customer expectations are exceeded. Our team comprise of over 70 staff of Designers, Consultants, Electricians who provide expert advice and quality of installation at an affordable price.</p>
    <span class="btn">READ MORE</span>
  </div>
</section>

<section class="why">
  <h2 class="section-title">Why Choose Us?</h2>
  <div class="why-rule"></div>
  <div class="reason red" style="left:98px"><svg viewBox="0 0 46 46"><path d="M26 4 12 26h10l-4 16 16-24H24z" fill="none" stroke="#fff" stroke-width="2.5" stroke-linejoin="round"/></svg>Professional<br>Service</div>
  <div class="reason dark" style="left:306px"><svg viewBox="0 0 46 46"><circle cx="23" cy="23" r="19" fill="none" stroke="#fff" stroke-width="3" stroke-dasharray="5 3"/><circle cx="23" cy="23" r="12" fill="none" stroke="#fff" stroke-width="2.5"/><path d="M17 23l4 4 8-8" fill="none" stroke="#fff" stroke-width="3"/></svg>5 year workmanship<br>guarantee</div>
  <div class="reason red" style="left:514px"><svg viewBox="0 0 46 46"><circle cx="20" cy="26" r="14" fill="none" stroke="#fff" stroke-width="2.5"/><text x="20" y="32" fill="#fff" font-size="17" font-family="Roboto" text-anchor="middle">$</text><path d="M34 4v14M30 8l4-4 4 4" fill="none" stroke="#fff" stroke-width="2.5"/></svg>Value for<br>Money</div>
  <div class="reason dark" style="left:722px"><svg viewBox="0 0 46 46"><path d="M23 6l7 12M30 18l-8 0M10 32l7-12M7 26l3 6 6-2M36 30H22M26 26l-4 4 4 4" fill="none" stroke="#fff" stroke-width="3" stroke-linecap="round"/></svg>Environmentally<br>friendly</div>
  <div class="reason red" style="left:930px"><svg viewBox="0 0 46 46"><circle cx="18" cy="26" r="9" fill="none" stroke="#fff" stroke-width="5" stroke-dasharray="4 3"/><circle cx="33" cy="13" r="6" fill="none" stroke="#fff" stroke-width="4" stroke-dasharray="3 2"/></svg>Fully<br>insured</div>
  <svg class="arrow" style="left:281px" width="20" height="10"><path d="M0 5h16M12 1l4 4-4 4" stroke="#333" fill="none" stroke-width="1.5"/></svg>
  <svg class="arrow" style="left:489px" width="20" height="10"><path d="M0 5h16M12 1l4 4-4 4" stroke="#333" fill="none" stroke-width="1.5"/></svg>
  <svg class="arrow" style="left:697px" width="20" height="10"><path d="M0 5h16M12 1l4 4-4 4" stroke="#333" fill="none" stroke-width="1.5"/></svg>
  <svg class="arrow" style="left:905px" width="20" height="10"><path d="M0 5h16M12 1l4 4-4 4" stroke="#333" fill="none" stroke-width="1.5"/></svg>
  <span class="pointer"></span>
  <div class="detail">
    <h3><b>2</b>5 year workmanship guarantee</h3>
    <p>You can buy with confidence as all of our work has a 5 year workmanship guarantee. For your peace of mind, we unconditionally back our electrical work. We will come back to fix any problems at our own expense.</p>
  </div>
</section>

<section class="clients">
  <h2 class="section-title">Our Satisfied Clients Include...</h2>
  <div class="client" style="left:285px">Velvetine</div>
  <div class="client" style="left:450px">Outback Surplus</div>
  <div class="client" style="left:615px">Heron Plumbing</div>
  <div class="client" style="left:780px">Golden Grill</div>
</section>

<section class="testimonials">
  <blockquote class="quote" style="left:100px">
    <div class="quote-photo" role="img" aria-label="Client building exterior" style="background:linear-gradient(180deg,#9db3cf,#c9b7a6)"></div>
    <div class="quote-body">
      <p>" Varno Electrical was pleasantly efficient, cost effective and delivered the desired results we were after, we look forward to seeing an ongoing benefit from dealing with them when we pay the Electrical bill going forward.</p>
      <cite>Colin Marsh<br>General Manager Plastrex</cite>
    </div>
    <span class="quote-mark">”</span>
  </blockquote>
  <blockquote class="quote" style="left:637px">
    <div class="quote-photo" role="img" aria-label="Client store front" style="background:linear-gradient(180deg,#e2c23c,#5a4c3a)"></div>
    <div class="quote-body">
      <p>" The service, communication and after sales service of Varno Electrical has been awesome. We would strongly recommend them to any business contemplating upgrading their lighting or any other electrical work</p>
      <cite>Dana Whitlow<br>Executive Outback Surplus</cite>
    </div>
    <span class="quote-mark">”</span>
  </blockquote>
</section>

<footer class="site-footer">
  <div class="foot-brand">
    <div class="brand-name">VARNO</div><div class="brand-tag">Spark Every Day</div>
    <address>12/48 LARKIN ST<br>GLENVALE VIC 3150</address>
    <div class="foot-line"><svg width="16" height="16" viewBox="0 0 16 16"><path d="M3 2c1-1 2-1 3 0l1 3-2 1c1 2 2 3 4 4l1-2 3 1c1 1 1 2 0 3-2 2-5 1-8-2S1 4 3 2z" fill="none" stroke="#ddd" stroke-width="1.2"/></svg>Phone: 139057</div>
    <div class="foot-line"><svg width="16" height="12" viewBox="0 0 16 12"><rect x=".5" y=".5" width="15" height="11" fill="none" stroke="#ddd"/><path d="M.5.5 8 7l7.5-6.5" fill="none" stroke="#ddd"/></svg>service@varnoelectrical-example.com.au</div>
  </div>
  <div class="newsletter">
    <h4>Join our newsletter</h4>
    <p>Sed ut perspiciatis unde omnis iste natus error sit voluptatem accusantium dolore</p>
    <div class="field">Enter Email</div>
    <span class="btn">SUBSCRIBE</span>
  </div>
  <ul class="links">
    <h4>Quick Links</h4>
    <li>Home</li><li>Varno Story</li><li>Our Work</li><li>Contact Us</li><li>Electrical</li><li>Led Lighting</li><li>Solar Power</li>
  </ul>
  <ul class="social">
    <h4>Social</h4>
    <li>Friendwall</li><li>Chirper</li><li>Circlet</li><li>Clipcast</li>
  </ul>
  <p class="copyright">Copyright 2017 | All Rights Reserved -- Varno Electrical.</p>
</footer>

</body>
</html>
```